English and Spanish Language School Needs a Business Card

Need a business card design a startup company called Maribel Language School. The company will offer English and Spanish conversational level courses designed to make the learner feel comfortable with grammar and vocabulary. We would like to see a logo with some colour that should communicate learning, growth.

Target Market(s)

Consumers and businesses

Industry/Entity Type

Education

Contact Information for Business Card

TBD

Font styles to use
Serif

Requirements
Must have
• Include the following
• Logo
• Name
• Title
• Cellphone Number
• Office Phone number
• Email address
• Office Address

```html
<!DOCTYPE html>
<html lang="en">
<head>
<meta charset="utf-8">
<title>Maribel Language School – Business Card</title>
<link href="https://fonts.googleapis.com/css2?family=Tinos:wght@400;700&display=swap" rel="stylesheet">
<style>
  :root {
    --backdrop: #2b2b2b;
    --brand-red: #c81e26;
    --brand-teal: #00a3ad;
    --paper: #ffffff;
    --ink-grey: #6e6e6e;
  }
  * { margin: 0; padding: 0; box-sizing: border-box; }
  html, body {
    width: 1189px;
    height: 1200px;
    overflow: hidden;
    background: var(--backdrop);
    font-family: "Tinos", "Times New Roman", serif;
  }
  .card {
    position: absolute;
    left: 171px;
    width: 855px;
    height: 486px;
    overflow: hidden;
  }
  .card-front {
    top: 68px;
    background: var(--brand-red);
    display: flex;
    align-items: center;
    justify-content: center;
  }
  .front-wordmark {
    color: var(--paper);
    text-align: center;
    font-weight: 700;
    line-height: 1;
  }
  .front-wordmark .wordmark-main { display: block; font-size: 104px; }
  .front-wordmark .wordmark-sub { display: block; font-size: 30px; margin-top: 8px; }

  .card-back {
    top: 627px;
    background: var(--paper);
  }
  .back-shapes {
    position: absolute;
    inset: 0;
    width: 855px;
    height: 486px;
  }
  .back-wordmark {
    position: absolute;
    left: 39px;
    top: 42px;
    color: var(--brand-red);
    font-weight: 700;
    line-height: 1;
  }
  .back-wordmark .wordmark-main { display: block; font-size: 118px; }
  .back-wordmark .wordmark-sub { display: block; font-size: 30px; margin-top: 6px; margin-left: 40px; }

  .holder {
    position: absolute;
    left: 44px;
    top: 233px;
  }
  .holder-name {
    color: var(--brand-red);
    font-weight: 700;
    font-size: 26px;
    line-height: 1;
  }
  .holder-title {
    color: var(--ink-grey);
    font-size: 21px;
    line-height: 1;
    margin-top: 2px;
  }
  .contact {
    position: absolute;
    left: 44px;
    top: 302px;
    color: var(--ink-grey);
    font-size: 22px;
    list-style: none;
  }
  .contact li { line-height: 31px; display: flex; align-items: center; gap: 4px; }
  .contact .address-line + .address-line { margin-bottom: 2px; }
  .contact-icon { width: 24px; height: 24px; flex: none; }
</style>
</head>
<body>

<section class="card card-front" aria-label="Business card front">
  <div class="front-wordmark">
    <span class="wordmark-main">Maribel</span>
    <span class="wordmark-sub">Language School</span>
  </div>
</section>

<section class="card card-back" aria-label="Business card back">
  <svg class="back-shapes" viewBox="0 0 855 486" aria-hidden="true">
    <path d="M693 0 C745 75 778 165 772 255 C766 345 730 420 683 486 L855 486 L855 0 Z" fill="var(--brand-red)"/>
    <path d="M757 228 C748 345 650 455 518 486 L668 486 C725 415 755 330 757 228 Z" fill="var(--brand-teal)"/>
  </svg>

  <div class="back-wordmark">
    <span class="wordmark-main">Maribel</span>
    <span class="wordmark-sub">Language School</span>
  </div>

  <div class="holder">
    <p class="holder-name">DANIEL REYES</p>
    <p class="holder-title">Manager</p>
  </div>

  <ul class="contact">
    <li class="address-line">Your Address, 2nd Ste</li>
    <li class="address-line">Cedarbrook, Texas 1234</li>
    <li>
      <svg class="contact-icon" viewBox="0 0 24 24" aria-label="Mobile">
        <rect width="24" height="24" fill="var(--brand-red)"/>
        <rect x="8" y="3" width="8" height="18" rx="1.5" fill="var(--paper)"/>
        <rect x="9.5" y="5" width="5" height="5" fill="var(--brand-red)"/>
      </svg>
      123 456 7890
    </li>
    <li>
      <svg class="contact-icon" viewBox="0 0 24 24" aria-label="Office phone">
        <rect width="24" height="24" fill="var(--brand-red)"/>
        <path d="M4 10 C4 6 20 6 20 10 L17 11 L16 9 L8 9 L7 11 Z" fill="var(--paper)"/>
        <path d="M7 12 L17 12 L19 19 L5 19 Z" fill="var(--paper)"/>
      </svg>
      123 456 7890
    </li>
    <li>
      <svg class="contact-icon" viewBox="0 0 24 24" aria-label="Email">
        <rect width="24" height="24" fill="var(--brand-red)"/>
        <rect x="4" y="7" width="16" height="11" fill="none" stroke="var(--paper)" stroke-width="1.6"/>
        <path d="M4 7 L12 13 L20 7 M4 18 L10 12 M20 18 L14 12" fill="none" stroke="var(--paper)" stroke-width="1.4"/>
      </svg>
      your@yourcompany.com
    </li>
  </ul>
</section>

</body>
</html>
```